Stonebridge Building and Projects business cards

A business card with watermark background (construction work)

Company logo attached

Home improvement projects
House renovations
Bathroom and kitchen renovations
House extensions
New builds and granny flats

Director Omar Haddani
(Phone number)
omar@sbpbuilding.com.au
(Instagram logo) sbp_building

```html
<!DOCTYPE html>
<html lang="en">
<head>
<meta charset="utf-8">
<title>Stonebridge Building and Projects – Business Cards</title>
<link href="https://fonts.googleapis.com/css2?family=Roboto:wght@400;500;700&family=Fira+Sans+Condensed:wght@600&display=swap" rel="stylesheet">
<style>
  :root {
    --bg: #2b2c2e;
    --card: #f8f8f8;
    --brand-blue: #0a72bb;
    --ink: #2a2a2a;
    --shade: #3b3d40;
    --faint: #ececec;
    --white: #ffffff;
  }
  * { box-sizing: border-box; margin: 0; padding: 0; }
  html, body { width: 1138px; height: 1200px; overflow: hidden; }
  body { background: var(--bg); font-family: "Roboto", sans-serif; position: relative; }

  .card {
    position: absolute; top: 288px; width: 376px; height: 622px;
    background: var(--card); border-radius: 16px; overflow: hidden;
    box-shadow: 0 10px 24px rgba(0,0,0,.45);
  }
  .card--front { left: 166px; }
  .card--back { left: 604px; }

  .watermark {
    position: absolute; left: 0; top: 0; width: 330px; height: 580px;
    background: linear-gradient(135deg, rgba(225,225,225,.55), rgba(240,240,240,.15));
  }

  .brand { position: absolute; left: 0; right: 0; text-align: center; font-family: "Roboto", sans-serif; font-weight: 700; }
  .brand__name { font-size: 44px; line-height: 1; letter-spacing: .5px; }
  .brand__sub { font-size: 20px; line-height: 1.2; margin-top: 8px; }
  .brand__tag { font-size: 19px; margin-top: 8px; display: inline-block; padding-bottom: 3px; border-bottom: 2px solid currentColor; }
  .card--front .brand { top: 118px; color: var(--brand-blue); }
  .card--back .brand { top: 66px; color: var(--white); }

  .services { position: absolute; top: 364px; left: 0; right: 0; list-style: none; text-align: center; color: var(--ink); font-size: 16.5px; }
  .services li { height: 32px; }
  .services span { display: inline-block; padding: 0 10px 5px; border-bottom: 1.5px solid var(--brand-blue); }
  .services li.services__pair span { border-bottom: none; padding: 0; }
  .services .sep { color: var(--brand-blue); margin: 0 8px; }

  .social { position: absolute; left: 0; right: 0; text-align: center; font-size: 16.5px; color: var(--ink); display: flex; justify-content: center; align-items: center; gap: 10px; }
  .social__dot { width: 14px; height: 14px; border-radius: 50%; background: var(--brand-blue); }
  .card--front .social { top: 518px; }
  .card--back .social { top: 554px; }

  .footer-band { position: absolute; left: 0; right: 0; bottom: 0; height: 47px; background: var(--brand-blue); color: var(--white); font-size: 16.5px; text-align: center; line-height: 47px; }

  .header-wave { position: absolute; left: 0; top: 0; }

  .person { position: absolute; top: 342px; left: 0; right: 0; text-align: center; }
  .person__name { font-family: "Fira Sans Condensed", sans-serif; font-weight: 600; font-size: 28px; color: var(--brand-blue); }
  .person__role { font-size: 17px; color: var(--ink); margin-top: 2px; }

  .contact-icons { position: absolute; top: 424px; left: 0; right: 0; display: flex; justify-content: center; align-items: center; gap: 4px; }
  .contact-icons .rule { width: 60px; height: 2px; background: var(--ink); margin: 0 16px; border-radius: 1px; }
  .contact-icons svg { width: 25px; height: 25px; }

  .contact { position: absolute; top: 463px; left: 0; right: 0; text-align: center; font-size: 16.5px; color: var(--ink); line-height: 24px; }
  .contact .accent { color: var(--brand-blue); }
</style>
</head>
<body>

<section class="card card--front">
  <div class="watermark" role="img" aria-label="Faint watermark of construction work"></div>
  <div class="brand">
    <div class="brand__name">Stonebridge</div>
    <div class="brand__sub">Building and Projects</div>
    <div class="brand__tag">Built right, every time</div>
  </div>
  <ul class="services">
    <li><span>Home Improvement Projects</span></li>
    <li><span>Bathroom &amp; Kitchen Renovations</span></li>
    <li><span>New Builds &amp; Granny Flats</span></li>
    <li class="services__pair"><span>House Renovations</span><b class="sep">|</b><span>House Extensions</span></li>
  </ul>
  <div class="social"><i class="social__dot"></i>sbp_building</div>
  <div class="footer-band">www.sbpbuilding.com.au</div>
</section>

<section class="card card--back">
  <svg class="header-wave" width="376" height="310" viewBox="0 0 376 310" aria-hidden="true">
    <path d="M0 262 Q170 330 376 250 L376 214 Q180 330 0 244 Z" fill="var(--shade)"/>
    <path d="M0 0 H376 V214 Q180 330 0 244 Z" fill="var(--brand-blue)"/>
  </svg>
  <div class="brand">
    <div class="brand__name">Stonebridge</div>
    <div class="brand__sub">Building and Projects</div>
    <div class="brand__tag">Built right, every time</div>
  </div>
  <div class="person">
    <div class="person__name">Omar Haddani</div>
    <div class="person__role">Managing Director</div>
  </div>
  <div class="contact-icons">
    <span class="rule"></span>
    <svg viewBox="0 0 26 26" aria-label="Phone"><circle cx="13" cy="13" r="11.5" fill="none" stroke="var(--brand-blue)" stroke-width="2"/><path d="M7 11 Q13 6 19 11 L17 13 L15 11.5 H11 L9 13 Z M9 14 H17 V18 H9 Z" fill="var(--brand-blue)"/></svg>
    <svg viewBox="0 0 26 26" aria-label="Email"><circle cx="13" cy="13" r="11.5" fill="none" stroke="var(--brand-blue)" stroke-width="2"/><rect x="7" y="9" width="12" height="8.5" rx="1" fill="var(--brand-blue)"/><path d="M7.5 9.5 L13 14 L18.5 9.5" fill="none" stroke="var(--white)" stroke-width="1.2"/></svg>
    <svg viewBox="0 0 26 26" aria-label="Website"><circle cx="13" cy="13" r="11.5" fill="none" stroke="var(--brand-blue)" stroke-width="2"/><g fill="none" stroke="var(--brand-blue)" stroke-width="1.3"><circle cx="13" cy="13" r="6.5"/><ellipse cx="13" cy="13" rx="3" ry="6.5"/><path d="M6.5 13 H19.5 M7.5 10 H18.5 M7.5 16 H18.5"/></g></svg>
    <span class="rule"></span>
  </div>
  <div class="contact">
    <div>0400 318 274</div>
    <div>omar@sbpbuilding.com.au</div>
    <div>www.<span class="accent">sbpbuilding</span>.com.au</div>
  </div>
  <div class="social"><i class="social__dot"></i>sbp_building</div>
</section>

</body>
</html>
```